Marcus Delbridge Finance

Need a personal website advertising Equipment Finance,Business Finance,Commercial Finance, Construction Finance, Bridging Finance. Similar websites are www.corvalend.com.au / www.tarmivest.com.au / www.qbr7.com.au /wwwhalvecredit.com.au

Target Market(s)

Business People

Industry/Entity Type

Business

Number of Pages Required

3 page

Font styles to use
Serif
Sans Serif

Requirements
Must have
• All i want is a simple corporate looking website advertising Equipment Finance, Commercial Finance, Construction Finance, Business Finance, Bridging Finance,

```html
<!DOCTYPE html>
<html lang="en">
<head>
<meta charset="utf-8">
<title>Marcus Delbridge Finance</title>
<link rel="stylesheet" href="https://fonts.googleapis.com/css2?family=Open+Sans:wght@400;600;700&family=Roboto+Condensed:wght@400;700&display=swap">
<style>
:root{
  --green:#a5c22b;
  --blue:#1a86b9;
  --text:#555;
  --muted:#777;
  --band:#ebebeb;
  --field:#f1f1f1;
  --field-line:#d4d4d4;
  --white:#fff;
}
*{box-sizing:border-box;margin:0;padding:0}
html,body{width:1200px;height:2740px;overflow:hidden;background:var(--white)}
body{position:relative;font-family:"Open Sans",Arial,sans-serif;color:var(--text);font-size:15px}
.abs{position:absolute}
.heading{font-family:"Roboto Condensed","Arial Narrow",sans-serif;font-weight:400;font-size:41px;letter-spacing:.5px;text-transform:uppercase;text-align:center;color:var(--green)}
.heading span{color:var(--blue)}

/* header */
.brand{left:79px;top:18px;color:var(--blue);font-family:"Open Sans",Arial,sans-serif;font-weight:400;font-size:36px;line-height:40px}
.brand small{display:block;font-size:22px;letter-spacing:9px;line-height:28px}
.top-phone{right:80px;top:10px;display:flex;align-items:center;gap:10px;color:var(--blue);font-weight:700;font-size:22px}
.nav{right:99px;top:58px;display:flex;gap:52px;font-size:19px;color:#444}
.nav .active{color:var(--blue)}

.hero{left:0;top:117px;width:1200px;height:571px;background:linear-gradient(120deg,#c9d6df 0%,#eef2f5 35%,#9aa7b3 65%,#dfe6ea 100%)}

/* services */
.services-title{left:0;top:738px;width:1200px}
.services-intro{left:240px;top:804px;width:720px;text-align:center;font-size:15px;line-height:26px}
.service{top:874px;width:190px;text-align:center}
.service .ring{width:114px;height:114px;margin:0 auto;border:2px solid var(--green);border-radius:50%;display:flex;align-items:center;justify-content:center}
.service h3{margin-top:20px;font-family:"Roboto Condensed","Arial Narrow",sans-serif;font-weight:400;font-size:24px;color:var(--blue)}
.service p{margin-top:4px;font-size:15px;line-height:25px}

/* welcome */
.welcome{left:0;top:1185px;width:1200px;height:417px;background:var(--band)}
.welcome h2{position:absolute;left:79px;top:62px;font-family:"Roboto Condensed","Arial Narrow",sans-serif;font-weight:400;font-size:39px;line-height:54px;color:var(--green);text-transform:uppercase}
.welcome h2 span{display:block;color:var(--blue)}
.welcome p{position:absolute;left:79px;top:182px;width:625px;font-size:15px;line-height:26px}
.btn{display:inline-flex;align-items:center;justify-content:center;background:var(--green);color:var(--white);font-weight:700;font-size:19px;text-transform:uppercase}
.welcome .btn{position:absolute;left:79px;top:287px;width:171px;height:55px}
.video{position:absolute;left:738px;top:68px;width:385px;height:270px;background:linear-gradient(135deg,#8c9291 0%,#d7dbdb 45%,#a6a39c 100%)}

/* news */
.news-title{left:0;top:1650px;width:1200px}
.news-card{top:1719px;width:235px}
.news-card .thumb{width:235px;height:144px}
.news-card h4{margin-top:16px;font-size:15px;font-weight:600;color:var(--blue)}
.news-card time{display:flex;align-items:center;gap:6px;font-size:14px;color:#999;margin-top:2px}
.news-card p{font-size:15px;line-height:25px;margin-top:2px}

/* call band */
.call{left:0;top:2048px;width:599px;height:124px;background:var(--green);display:flex;align-items:center;justify-content:center;gap:12px;color:var(--white)}
.call .label{font-family:"Roboto Condensed","Arial Narrow",sans-serif;font-size:38px}
.call .number{font-family:"Roboto Condensed","Arial Narrow",sans-serif;font-weight:700;font-size:40px}
.call-note{left:599px;top:2048px;width:601px;height:124px;background:var(--blue);color:var(--white);padding:16px 0 0 22px;font-size:15px;line-height:26px}
.call-note .mail{display:flex;align-items:center;gap:10px;margin-top:8px}

/* quote */
.quote-title{left:0;top:2220px;width:1200px}
.field{background:var(--field);border:1px solid var(--field-line);border-radius:3px;font-size:14px;color:#666;padding:12px 10px}
.submit{left:77px;top:2564px;width:135px;height:57px}
.contact-item{left:772px;display:flex;align-items:center;gap:20px;font-size:15px;line-height:25px}
.icon-ring{width:52px;height:52px;border:2px solid var(--green);border-radius:50%;display:flex;align-items:center;justify-content:center;flex:none}
.social{left:775px;top:2509px;display:flex;gap:10px}
.social i{width:47px;height:47px;border:2px solid var(--green);border-radius:50%;display:block}
.social i:first-child{background:var(--green)}

.footer{left:0;top:2678px;width:1200px;height:62px;background:var(--blue);color:var(--white);display:flex;align-items:center;justify-content:center;font-size:15px}
.footer b{color:var(--green);font-weight:700;margin:0 4px}
</style>
</head>
<body>

<header>
  <div class="abs brand">Marcus Delbridge<small>Finance</small></div>
  <div class="abs top-phone">
    <svg width="24" height="24" viewBox="0 0 24 24"><path fill="#222" d="M6.6 10.8a15.1 15.1 0 0 0 6.6 6.6l2.2-2.2a1 1 0 0 1 1-.25 11.4 11.4 0 0 0 3.6.57 1 1 0 0 1 1 1V20a1 1 0 0 1-1 1A17 17 0 0 1 3 4a1 1 0 0 1 1-1h3.5a1 1 0 0 1 1 1c0 1.25.2 2.45.57 3.57a1 1 0 0 1-.25 1z"/></svg>
    123 456 7890
  </div>
  <nav class="abs nav"><span class="active">HOME</span><span>ABOUT</span><span>SERVICES</span><span>CONTACT</span></nav>
</header>

<div class="abs hero" role="img" aria-label="Photo of business people meeting around an office table"></div>

<section>
  <h2 class="abs heading services-title">Services <span>We Provide</span></h2>
  <p class="abs services-intro">Lorem Ipsum is dummy text of the printing and typesetting industry. Lorem Ipsum has been the industry's standard dummy text ever since the 1500.</p>

  <div class="abs service" style="left:78px">
    <div class="ring"><svg width="60" height="60" viewBox="0 0 60 60" fill="none" stroke="#a5c22b" stroke-width="3"><circle cx="30" cy="30" r="24"/><ellipse cx="30" cy="30" rx="11" ry="24"/><path d="M6 30h48M10 18h40M10 42h40"/></svg></div>
    <h3>Equipment</h3><p>Lorem Ipsum is dummy text of the printing and typesetting industry.</p>
  </div>
  <div class="abs service" style="left:290px">
    <div class="ring"><svg width="64" height="60" viewBox="0 0 64 60" fill="#a5c22b"><rect x="4" y="40" width="9" height="16"/><rect x="18" y="32" width="9" height="24"/><rect x="32" y="36" width="9" height="20"/><rect x="46" y="24" width="9" height="32"/><path d="M4 34 22 18l12 10 16-16" fill="none" stroke="#a5c22b" stroke-width="4"/><path d="M42 6h16v16z"/></svg></div>
    <h3>Business</h3><p>Lorem Ipsum is dummy text of the printing and typesetting industry.</p>
  </div>
  <div class="abs service" style="left:502px">
    <div class="ring"><svg width="64" height="50" viewBox="0 0 64 50" fill="#a5c22b"><path d="M2 14 14 8l6 18-10 6z"/><path d="M62 14 50 8l-6 18 10 6z"/><path d="M18 12h14l10 10-4 4-8-6-8 8z"/><path d="M44 14 54 28 40 42 28 32l6-6 6 4z"/></svg></div>
    <h3>Commercial</h3><p>Lorem Ipsum is dummy text of the printing and typesetting industry.</p>
  </div>
  <div class="abs service" style="left:718px">
    <div class="ring"><svg width="64" height="64" viewBox="0 0 64 64" fill="#a5c22b"><rect x="6" y="22" width="16" height="36"/><rect x="24" y="8" width="18" height="50"/><rect x="44" y="28" width="14" height="30"/><g fill="#fff"><rect x="10" y="28" width="3" height="4"/><rect x="15" y="28" width="3" height="4"/><rect x="10" y="38" width="3" height="4"/><rect x="15" y="38" width="3" height="4"/><rect x="28" y="14" width="4" height="5"/><rect x="35" y="14" width="4" height="5"/><rect x="28" y="26" width="4" height="5"/><rect x="35" y="26" width="4" height="5"/><rect x="28" y="38" width="4" height="5"/><rect x="35" y="38" width="4" height="5"/><rect x="48" y="34" width="3" height="4"/><rect x="53" y="34" width="3" height="4"/></g></svg></div>
    <h3>Construction</h3><p>Lorem Ipsum is dummy text of the printing and typesetting industry.</p>
  </div>
  <div class="abs service" style="left:933px">
    <div class="ring"><svg width="66" height="40" viewBox="0 0 66 40" fill="none" stroke="#a5c22b" stroke-width="3"><path d="M2 28h62M20 4v30M46 4v30M20 4 4 28M20 4l14 24M46 4 32 28M46 4l16 24"/></svg></div>
    <h3>Bridging</h3><p>Lorem Ipsum is dummy text of the printing and typesetting industry.</p>
  </div>
</section>

<section class="abs welcome">
  <h2>Welcome to<span>Marcus Delbridge Finance</span></h2>
  <p>Lorem Ipsum is dummy text of the printing and typesetting industry. Lorem Ipsum has been the industry's standard dummy text ever since the 1500s, when an unknown printer took a galley of type it to make a type specimen book.</p>
  <span class="btn">Read More</span>
  <div class="video" role="img" aria-label="Video still of colleagues working together in an office"></div>
</section>

<section>
  <h2 class="abs heading news-title">Latest <span>News</span></h2>
  <article class="abs news-card" style="left:86px">
    <div class="thumb" role="img" aria-label="Photo of a business handshake" style="background:linear-gradient(135deg,#3b4654,#b7c0ca)"></div>
    <h4>Lorem Ipsum is dummy text.</h4>
    <time><svg width="11" height="11" viewBox="0 0 11 11" fill="#999"><rect x="0" y="2" width="11" height="9"/><rect x="2" y="0" width="2" height="3"/><rect x="7" y="0" width="2" height="3"/></svg>09 January 2017</time>
    <p>Lorem Ipsum is dummy text of the printing and typesetting industry standard.</p>
  </article>
  <article class="abs news-card" style="left:358px">
    <div class="thumb" role="img" aria-label="Photo of a hand using a tablet with charts" style="background:linear-gradient(135deg,#e6eef3,#9ec3dc)"></div>
    <h4>Lorem Ipsum is dummy text.</h4>
    <time><svg width="11" height="11" viewBox="0 0 11 11" fill="#999"><rect x="0" y="2" width="11" height="9"/><rect x="2" y="0" width="2" height="3"/><rect x="7" y="0" width="2" height="3"/></svg>09 January 2017</time>
    <p>Lorem Ipsum is dummy text of the printing and typesetting industry standard.</p>
  </article>
  <article class="abs news-card" style="left:628px">
    <div class="thumb" role="img" aria-label="Photo of a long bridge over water at dusk" style="background:linear-gradient(180deg,#4f7aa6,#a9c0d4 60%,#d8b98d)"></div>
    <h4>Lorem Ipsum is dummy text.</h4>
    <time><svg width="11" height="11" viewBox="0 0 11 11" fill="#999"><rect x="0" y="2" width="11" height="9"/><rect x="2" y="0" width="2" height="3"/><rect x="7" y="0" width="2" height="3"/></svg>09 January 2017</time>
    <p>Lorem Ipsum is dummy text of the printing and typesetting industry standard.</p>
  </article>
  <article class="abs news-card" style="left:899px">
    <div class="thumb" role="img" aria-label="Photo of a team meeting in a bright office" style="background:linear-gradient(135deg,#dfe5e8,#8d9aa4)"></div>
    <h4>Lorem Ipsum is dummy text.</h4>
    <time><svg width="11" height="11" viewBox="0 0 11 11" fill="#999"><rect x="0" y="2" width="11" height="9"/><rect x="2" y="0" width="2" height="3"/><rect x="7" y="0" width="2" height="3"/></svg>09 January 2017</time>
    <p>Lorem Ipsum is dummy text of the printing and typesetting industry standard.</p>
  </article>
</section>

<section>
  <div class="abs call">
    <span class="label">CALL US</span>
    <svg width="58" height="58" viewBox="0 0 58 58"><circle cx="29" cy="29" r="26" fill="none" stroke="#fff" stroke-width="3"/><path fill="#fff" d="M21.5 26.5a15 15 0 0 0 10 10l3-3a1.4 1.4 0 0 1 1.4-.35 9 9 0 0 0 3.4.6 1.3 1.3 0 0 1 1.3 1.3v4.6a1.3 1.3 0 0 1-1.3 1.3A21 21 0 0 1 17.8 20.7a1.3 1.3 0 0 1 1.3-1.3h4.6a1.3 1.3 0 0 1 1.3 1.3c0 1.2.2 2.3.6 3.4a1.4 1.4 0 0 1-.35 1.4z"/></svg>
    <span class="number">123 456 7890</span>
  </div>
  <div class="abs call-note">
    Lorem Ipsum is dummy text of the printing and typesetting industry.<br>Lorem Ipsum has been the industry's standard dummy text ever.
    <div class="mail"><svg width="20" height="15" viewBox="0 0 20 15" fill="none" stroke="#fff" stroke-width="1.6"><rect x="1" y="1" width="18" height="13" rx="1"/><path d="m1 2 9 7 9-7"/></svg>info@marcusdelbridge.com</div>
  </div>
</section>

<section>
  <h2 class="abs heading quote-title">Get a <span>Free Quote</span></h2>
  <div class="abs field" style="left:77px;top:2289px;width:307px;height:45px">Enter Name</div>
  <div class="abs field" style="left:405px;top:2289px;width:307px;height:45px">Enter Contact No.</div>
  <div class="abs field" style="left:77px;top:2356px;width:635px;height:46px">Enter Email</div>
  <div class="abs field" style="left:77px;top:2424px;width:635px;height:119px">Enter Message</div>
  <span class="abs btn submit">Submit</span>

  <div class="abs contact-item" style="top:2290px">
    <span class="icon-ring"><svg width="18" height="24" viewBox="0 0 18 24"><path fill="#a5c22b" d="M9 0a9 9 0 0 0-9 9c0 6.5 9 15 9 15s9-8.5 9-15a9 9 0 0 0-9-9zm0 12.5A3.5 3.5 0 1 1 9 5.5a3.5 3.5 0 0 1 0 7z"/></svg></span>
    <span>Lorem Ipsum is simply<br>dummy text of the printing.</span>
  </div>
  <div class="abs contact-item" style="top:2359px;font-weight:600;color:#333">
    <span class="icon-ring"><svg width="22" height="22" viewBox="0 0 24 24"><path fill="#a5c22b" d="M6.6 10.8a15.1 15.1 0 0 0 6.6 6.6l2.2-2.2a1 1 0 0 1 1-.25 11.4 11.4 0 0 0 3.6.57 1 1 0 0 1 1 1V20a1 1 0 0 1-1 1A17 17 0 0 1 3 4a1 1 0 0 1 1-1h3.5a1 1 0 0 1 1 1c0 1.25.2 2.45.57 3.57a1 1 0 0 1-.25 1z"/></svg></span>
    <span>123 456 7890</span>
  </div>
  <div class="abs contact-item" style="top:2432px">
    <span class="icon-ring"><svg width="22" height="16" viewBox="0 0 20 15" fill="none" stroke="#a5c22b" stroke-width="1.8"><rect x="1" y="1" width="18" height="13" rx="1"/><path d="m1 2 9 7 9-7"/></svg></span>
    <span>info@marcusdelbridge.com</span>
  </div>
  <div class="abs social"><i></i><i></i><i></i></div>
</section>

<footer class="abs footer">© <b>Marcus Delbridge</b> - 2017. All Rights Reserved.</footer>

</body>
</html>
```